Talon Microsystems PowerPoint Master Slide Deck Design

This is a 2-phase project to design a slide deck for a semiconductor company in the Silicon Valley. The design budget will be increased with each phase.
The slide deck will need to have one version with a dark background for presentations and a second version with a white background. Otherwise, the slides will be the same. I anticipate we will need a total of 10 slides, but that number may change.
The first phase will be to design a Title and a Title and Content slide.
- The Title Slide is the first slide of the deck. It should include the presentation title, the presenter's name and date of presentation
- The Title and Content slide should include a title and content with bullet points and up to 2 additional sub-bullets
- The Title and Content slide should have a footer that includes the slide #, Talon Microsystems Confidential, and the logo. This footer will be on every slide except the Title Slide
The first two slides will serve as the format for the remaining ~8 slides:
-Header and Content Text (1, 2, 4 column)
-Header and Content Image (bar chart, pie chart, tables)
-Break
-Title only
-Closing (Talon logo only)
Our slides contain a lot of content so a clean and simple design is best.
Both phases will need to include pre-set color options for
-Text and Lines
-Shadows
-Bullets and sub-bullets (including shapes, ex. circle, slash, square, etc.)
-Bar charts, pie charts, tables
Samples of our collateral are attached. Logo files are also attached
Look and feel
Each slider illustrates characteristics of the customer's brand and the style your logo design should communicate.

```html
<!DOCTYPE html>
<html lang="en">
<head>
<meta charset="utf-8">
<title>Talon Microsystems Slide Deck</title>
<link href="https://fonts.googleapis.com/css2?family=Roboto:ital,wght@0,400;0,500;0,700;1,400&display=swap" rel="stylesheet">
<style>
:root{
  --royal:#0b1ff0;
  --royal-deep:#0718c8;
  --sky:#17a8f7;
  --ink:#1b1b24;
  --body:#55575f;
  --muted:#6a6c74;
  --track:#eef1f7;
  --page:#ffffff;
  --night:#06070d;
}
*{margin:0;padding:0;box-sizing:border-box}
html,body{width:1200px;height:4112px;overflow:hidden;background:var(--page)}
body{position:relative;font-family:'Roboto',sans-serif;color:var(--ink)}
.slide{position:absolute;left:66px;width:1072px;height:603px;background:var(--page);box-shadow:0 2px 14px rgba(20,30,60,.12);overflow:hidden}
.s1{top:64px}.s2{top:741px}.s3{top:1419px}.s4{top:2097px}.s5{top:2775px}.s6{top:3453px}

/* title slide */
.hero-bg{position:absolute;inset:0;background:
  radial-gradient(circle at 76% 44%,#f3b54a 0,#b06a1e 8%,#3a4a7a 20%,rgba(10,14,30,0) 38%),
  linear-gradient(135deg,#0c1020 0%,#07080f 45%,#10131d 100%)}
.hero-rule{position:absolute;left:0;right:0;bottom:0;height:5px;background:var(--royal)}
.wordmark{position:absolute;display:flex;align-items:center;gap:10px;font-weight:500;white-space:nowrap}
.wordmark .dot{border-radius:50%;border:3px solid currentColor}
.s1 .wordmark{left:90px;top:108px;color:#fff;font-size:34px}
.s1 .wordmark .dot{width:30px;height:30px;border-color:var(--royal)}
.hero-title{position:absolute;left:90px;top:300px;font-weight:700;font-size:60px;line-height:72px}
.hero-title .l1{color:#fff}.hero-title .l2{color:var(--royal)}
.presenter{position:absolute;left:90px;top:452px;color:#fff;font-size:26px;font-weight:500}
.date{position:absolute;left:90px;top:504px;color:#fff;font-size:15px}

/* content slides */
.heading{position:absolute;left:0;top:48px;height:55px;padding:0 50px;background:var(--royal);color:#fff;font-weight:700;font-size:24px;line-height:55px;border-radius:0 28px 28px 0;white-space:nowrap}
.copy{position:absolute;top:126px;width:463px;font-size:12.6px;line-height:22.5px;color:var(--body);text-align:justify}
.copy p+p{margin-top:22.5px}
.col-a{left:52px}.col-b{left:558px}

.footer{position:absolute;left:0;right:0;bottom:0;height:70px;background:linear-gradient(90deg,var(--royal) 0%,var(--royal-deep) 35%,var(--sky) 100%);color:#fff}
.footer .wordmark{left:90px;top:22px;font-size:20px;color:#fff}
.footer .wordmark .dot{width:18px;height:18px;border-width:2px}
.footer .conf{position:absolute;left:0;right:0;top:0;text-align:center;line-height:70px;font-size:14px;font-weight:500}
.footer .page{position:absolute;left:846px;top:17px;width:136px;height:36px;border-radius:18px;background:var(--royal);text-align:center;line-height:36px;font-size:14px;font-weight:500}

.visual{position:absolute;left:579px;top:80px;width:403px;height:406px;border:6px solid #fff;border-radius:28px;box-shadow:0 3px 12px rgba(0,0,0,.22);
  background:radial-gradient(circle at 50% 55%,#f0a631 0,#a35b16 14%,#273043 34%,#0e1320 70%)}

.bars{position:absolute;left:550px;top:132px;width:432px}
.bar{position:relative;height:34px;margin-bottom:18px;border-radius:17px;background:var(--track);box-shadow:0 1px 4px rgba(0,0,0,.15)}
.bar i{position:absolute;left:0;top:0;bottom:0;border-radius:17px}
.bar.light i{background:var(--sky)}.bar.dark i{background:var(--royal)}
.bar b{position:absolute;right:18px;top:0;line-height:34px;font-size:11px;color:var(--royal-deep)}

.points{position:absolute;top:140px;width:460px}
.pa{left:54px}.pb{left:560px}
.point{position:relative;padding-left:30px;font-size:12px;line-height:19px;font-weight:700;color:var(--ink);text-align:justify;margin-bottom:10px}
.point::before{content:"";position:absolute;left:0;top:4px;width:11px;height:11px;border:2.5px solid var(--royal);border-radius:50%;box-sizing:border-box}
.point::after{content:"";position:absolute;left:3.5px;top:7.5px;width:4px;height:4px;background:var(--royal);border-radius:50%}
.sub{position:relative;padding-left:36px;font-size:11px;line-height:19px;font-style:italic;color:var(--muted);margin-bottom:14px}
.sub::before{content:"\00BB";position:absolute;left:8px;top:-1px;font-style:normal;font-weight:700;font-size:16px;color:var(--royal)}

/* closing */
.closing{background:linear-gradient(110deg,var(--royal) 0%,var(--royal) 35%,#1270f2 70%,#2ab0f8 100%)}
.closing .wordmark{left:0;right:0;top:240px;justify-content:center;color:#fff;font-size:88px;gap:26px}
.closing .wordmark .dot{width:70px;height:70px;border-width:8px}
</style>
</head>
<body>

<section class="slide s1">
  <div class="hero-bg" role="img" aria-label="Dark circuit board photograph with a glowing wireframe chip cube"></div>
  <div class="wordmark"><span class="dot"></span>Talon Microsystems</div>
  <h1 class="hero-title"><span class="l1">TALON</span><br><span class="l2">MICROSYSTEMS</span></h1>
  <p class="presenter">Presenter's Name : Daniel Reyes</p>
  <p class="date">13, December 2023</p>
  <div class="hero-rule"></div>
</section>

<section class="slide s2">
  <h2 class="heading">ABOUT TALON MICROSYSTEMS</h2>
  <div class="copy col-a">
    <p>Sed ut perspiciatis unde omnis iste natus error sit voluptatem accusantium doloremque laudantium, totam rem aperiam, eaque ipsa quae ab illo inventore veritatis et quasi architecto beatae vitae dicta sunt explicabo. Nemo enim ipsam voluptatem quia voluptas sit aspernatur aut odit aut fugit, sed quia consequuntur magni dolores eos qui ratione voluptatem sequi nesciunt. Neque porro quisquam est, qui dolorem ipsum quia dolor sit amet, consectetur, adipisci velit, sed quia non numquam eius modi tempora incidunt ut labore et dolore magnam aliquam quaerat voluptatem.</p>
    <p>Ut enim ad minima veniam, quis nostrum exercitationem ullam corporis suscipit laboriosam, nisi ut aliquid ex ea commodi consequatur? Quis autem vel eum iure reprehenderit qui in ea voluptate velit esse quam nihil molestiae consequatur, vel illum qui dolorem eum fugiat quo voluptas nulla pariatur?Sed ut perspiciatis unde omnis iste natus error sit voluptatem accusantium doloremque laudantium, totam rem aperiam, eaque ipsa quae ab illo inventore veritatis et quasi architecto beatae</p>
  </div>
  <div class="copy col-b">
    <p>Sed ut perspiciatis unde omnis iste natus error sit voluptatem accusantium doloremque laudantium, totam rem aperiam, eaque ipsa quae ab illo inventore veritatis et quasi architecto beatae vitae dicta sunt explicabo. Nemo enim ipsam voluptatem quia voluptas sit aspernatur aut odit aut fugit, sed quia consequuntur magni dolores eos qui ratione voluptatem sequi nesciunt. Neque porro quisquam est, qui dolorem ipsum quia dolor sit amet, consectetur, adipisci velit, sed quia non numquam eius modi tempora incidunt ut labore et dolore magnam aliquam quaerat voluptatem.</p>
    <p>Ut enim ad minima veniam, quis nostrum exercitationem ullam corporis suscipit laboriosam, nisi ut aliquid ex ea commodi consequatur? Quis autem vel eum iure reprehenderit qui in ea voluptate velit esse quam nihil molestiae consequatur, vel illum qui dolorem eum fugiat quo voluptas nulla pariatur?Sed ut perspiciatis unde omnis iste natus error sit voluptatem accusantium doloremque laudantium, totam rem aperiam, eaque ipsa quae ab illo inventore veritatis et quasi architecto beatae</p>
  </div>
  <footer class="footer"><div class="wordmark"><span class="dot"></span>Talon</div><div class="conf">Talon Microsystems Confidential</div><div class="page">Page 02 Of 06</div></footer>
</section>

<section class="slide s3">
  <h2 class="heading">WHAT WE DO</h2>
  <div class="copy col-a">
    <p>Sed ut perspiciatis unde omnis iste natus error sit voluptatem accusantium doloremque laudantium, totam rem aperiam, eaque ipsa quae ab illo inventore veritatis et quasi architecto beatae vitae dicta sunt explicabo. Nemo enim ipsam voluptatem quia voluptas sit aspernatur aut odit aut fugit, sed quia consequuntur magni dolores eos qui ratione voluptatem sequi nesciunt. Neque porro quisquam est, qui dolorem ipsum quia dolor sit amet, consectetur, adipisci velit, sed quia non numquam eius modi tempora incidunt ut labore et dolore magnam aliquam quaerat voluptatem.</p>
    <p>Ut enim ad minima veniam, quis nostrum exercitationem ullam corporis suscipit laboriosam, nisi ut aliquid ex ea commodi consequatur? Quis autem vel eum iure reprehenderit qui in ea voluptate velit esse quam nihil molestiae consequatur, vel illum qui dolorem eum fugiat quo voluptas nulla pariatur?Sed ut perspiciatis unde omnis iste natus error sit voluptatem accusantium doloremque laudantium, totam rem aperiam, eaque ipsa quae ab illo inventore veritatis et quasi architecto beatae</p>
  </div>
  <div class="visual" role="img" aria-label="Glowing orange processor chip on a dark circuit board"></div>
  <footer class="footer"><div class="wordmark"><span class="dot"></span>Talon</div><div class="conf">Talon Microsystems Confidential</div><div class="page">Page 03 Of 06</div></footer>
</section>

<section class="slide s4">
  <h2 class="heading">HOW TALON MICROSYSTEMS WORKS</h2>
  <div class="copy col-a">
    <p>Sed ut perspiciatis unde omnis iste natus error sit voluptatem accusantium doloremque laudantium, totam rem aperiam, eaque ipsa quae ab illo inventore veritatis et quasi architecto beatae vitae dicta sunt explicabo. Nemo enim ipsam voluptatem quia voluptas sit aspernatur aut odit aut fugit, sed quia consequuntur magni dolores eos qui ratione voluptatem sequi nesciunt. Neque porro quisquam est, qui dolorem ipsum quia dolor sit amet, consectetur, adipisci velit, sed quia non numquam eius modi tempora incidunt ut labore et dolore magnam aliquam quaerat voluptatem.</p>
    <p>Ut enim ad minima veniam, quis nostrum exercitationem ullam corporis suscipit laboriosam, nisi ut aliquid ex ea commodi consequatur? Quis autem vel eum iure reprehenderit qui in ea voluptate velit esse quam nihil molestiae consequatur, vel illum qui dolorem eum fugiat quo voluptas nulla pariatur?Sed ut perspiciatis unde omnis iste natus error sit voluptatem accusantium doloremque laudantium, totam rem aperiam, eaque ipsa quae ab illo inventore veritatis et quasi architecto beatae</p>
  </div>
  <div class="bars">
    <div class="bar light"><i style="width:56%"></i><b>60%</b></div>
    <div class="bar dark"><i style="width:70%"></i><b>80%</b></div>
    <div class="bar light"><i style="width:42%"></i><b>40%</b></div>
    <div class="bar dark"><i style="width:33%"></i><b>30%</b></div>
    <div class="bar light"><i style="width:65%"></i><b>70%</b></div>
    <div class="bar dark"><i style="width:55%"></i><b>60%</b></div>
    <div class="bar light"><i style="width:78%"></i><b>70%</b></div>
  </div>
  <footer class="footer"><div class="wordmark"><span class="dot"></span>Talon</div><div class="conf">Talon Microsystems Confidential</div><div class="page">Page 04 Of 06</div></footer>
</section>

<section class="slide s5">
  <h2 class="heading">WHY CHOOSE TALON MICROSYSTEMS</h2>
  <div class="points pa">
    <p class="point">Sed ut perspiciatis unde omnis iste natus error sit voluptatem accusantium doloremque laudantium, totam rem aperiam, eaque ipsa quae ab illo inventore veritatis et quasi architecto beatae vitae dicta sunt explicabo.</p>
    <p class="sub">Sed ut perspiciatis unde omnis iste natus error sit voluptatem accusantium doloremque laudantium, totam rem aperiam, eaque ipsa quae ab</p>
    <p class="sub">Illo inventore veritatis et quasi architecto beatae vitae dicta sunt explicabo. Nemo enim ipsam voluptatem quia voluptas sit aspernatur aut odit aut fugit, sed quia</p>
    <p class="point">Sed ut perspiciatis unde omnis iste natus error sit voluptatem accusantium doloremque laudantium, totam rem aperiam, eaque ipsa quae ab illo inventore veritatis et quasi architecto beatae vitae dicta sunt explicabo.</p>
    <p class="sub">Sed ut perspiciatis unde omnis iste natus error sit voluptatem accusantium doloremque laudantium, totam rem aperiam, eaque ipsa quae ab</p>
    <p class="sub">Illo inventore veritatis et quasi architecto beatae vitae dicta sunt explicabo. Nemo enim ipsam voluptatem quia voluptas sit aspernatur aut odit aut fugit, sed quia</p>
  </div>
  <div class="points pb">
    <p class="point">Sed ut perspiciatis unde omnis iste natus error sit voluptatem accusantium doloremque laudantium, totam rem aperiam, eaque ipsa quae ab illo inventore veritatis et quasi architecto beatae vitae dicta sunt explicabo.</p>
    <p class="sub">Sed ut perspiciatis unde omnis iste natus error sit voluptatem accusantium doloremque laudantium, totam rem aperiam, eaque ipsa quae ab</p>
    <p class="sub">Illo inventore veritatis et quasi architecto beatae vitae dicta sunt explicabo. Nemo enim ipsam voluptatem quia voluptas sit aspernatur aut odit aut fugit, sed quia</p>
    <p class="point">Sed ut perspiciatis unde omnis iste natus error sit voluptatem accusantium doloremque laudantium, totam rem aperiam, eaque ipsa quae ab illo inventore veritatis et quasi architecto beatae vitae dicta sunt explicabo.</p>
    <p class="sub">Sed ut perspiciatis unde omnis iste natus error sit voluptatem accusantium doloremque laudantium, totam rem aperiam, eaque ipsa quae ab</p>
    <p class="sub">Illo inventore veritatis et quasi architecto beatae vitae dicta sunt explicabo. Nemo enim ipsam voluptatem quia voluptas sit aspernatur aut odit aut fugit, sed quia</p>
  </div>
  <footer class="footer"><div class="wordmark"><span class="dot"></span>Talon</div><div class="conf">Talon Microsystems Confidential</div><div class="page">Page 05 Of 06</div></footer>
</section>

<section class="slide s6 closing">
  <div class="wordmark"><span class="dot"></span>Talon Microsystems</div>
</section>

</body>
</html>
```